KORVAX Flyer

We need a flyer for the research project called 'KORVAX'. We will distribute this flyer during conferences and events to our audience (mainly industry (Security and IoT), medical organisations, and researchers) in order to provide the basic information about the project.
The project will provide a Universal Cyber Security Toolkit for the Health-Care Industry.
We are attaching files to provide with concrete information on our requirements:
- KORVAX brochure content_final.ppt: includes the content we would like to include in the flyer. There is also the URL to the project website
- KORVAX layout.doc: it includes information about the layout (example video from another project brochure)
- KORVAX logo final version_sourcefile.zip: the project logo
- Logo-partners.zip: Logos that will be included (please follow the numbered order.)
We would like to use colors that belong to the project logo color range. Regarding the images that you may include in the brochure we wouldn't like to propose any because we do not want to limitate your imagination. They could be relevant to medical devices, security, etc.

```html
<!DOCTYPE html>
<html lang="en">
<head>
<meta charset="utf-8">
<title>KORVAX Flyer</title>
<link rel="stylesheet" href="https://fonts.googleapis.com/css2?family=Titan+One&family=Fjalla+One&family=Roboto+Condensed:wght@700&display=swap">
<style>
  :root {
    --page-bg: #e9eef3;
    --paper: #ffffff;
    --panel: #d9e3ec;
    --slate: #7896a6;
    --slate-dark: #6b8595;
    --navy: #587ba0;
    --steel-photo: #b9c9d6;
    --ink: #111111;
    --logo-dark: #372c2c;
    --teal: #3fb6a8;
    --white: #ffffff;
  }
  * { box-sizing: border-box; margin: 0; padding: 0; }
  html, body { width: 1200px; height: 800px; overflow: hidden; }
  body { background: var(--page-bg); position: relative; }

  .flyer-frame {
    position: absolute;
    left: 355px; top: 22px;
    width: 594px; height: 916px;
    transform: scale(0.825);
    transform-origin: top left;
    background: var(--paper);
    box-shadow: 0 2px 10px rgba(0,0,0,0.18);
  }
  .flyer-art { position: absolute; left: 0; top: 0; }

  .brand-badge {
    position: absolute;
    left: 123px; top: 103px;
    width: 90px; height: 90px;
    border-radius: 50%;
    background: var(--logo-dark);
    border: 4px solid #9fb2bf;
    display: flex; align-items: center; justify-content: center;
  }
  .brand-name {
    font-family: "Fjalla One", sans-serif;
    font-size: 19px;
    color: var(--teal);
    letter-spacing: 0.5px;
  }

  .headline {
    position: absolute; left: 43px; width: 502px;
    font-family: "Titan One", sans-serif;
    font-weight: 400;
    font-size: 35px;
    line-height: 44px;
    letter-spacing: 2px;
    white-space: nowrap;
    color: var(--ink);
    border-bottom: 3px solid var(--ink);
    padding-bottom: 6px;
  }
  .headline-top { top: 525px; }
  .headline-bottom { top: 588px; }

  .tagline {
    position: absolute; left: 43px; top: 664px;
    font-family: "Fjalla One", sans-serif;
    font-size: 18px;
    letter-spacing: 1.2px;
    white-space: nowrap;
    color: var(--ink);
  }
  .audience-title {
    position: absolute; left: 43px; top: 720px;
    font-family: "Fjalla One", sans-serif;
    font-weight: 400;
    font-size: 24px;
    white-space: nowrap;
    color: var(--ink);
  }
  .audience-item {
    position: absolute;
    font-family: "Fjalla One", sans-serif;
    font-size: 18px;
    line-height: 22px;
    color: var(--ink);
    white-space: nowrap;
  }
  .audience-item::before {
    content: ""; display: inline-block;
    width: 6px; height: 6px; border-radius: 50%;
    background: var(--ink);
    margin-right: 6px; vertical-align: middle;
  }

  .contact-band {
    position: absolute; left: 16px; top: 870px;
    width: 564px; height: 33px;
    border-top: 3px solid var(--white);
    font-family: "Roboto Condensed", sans-serif;
    font-weight: 700;
    font-size: 8px;
    color: var(--ink);
  }
  .contact-line { position: absolute; white-space: nowrap; }
  .contact-line::before {
    content: ""; display: inline-block;
    width: 6px; height: 6px; border-radius: 50%;
    border: 1px solid var(--ink);
    margin-right: 4px; vertical-align: -1px;
  }
</style>
</head>
<body>
  <div class="flyer-frame">
    <svg class="flyer-art" width="594" height="916" viewBox="0 0 594 916">
      <defs>
        <linearGradient id="xray-tone" x1="0" y1="0" x2="1" y2="1">
          <stop offset="0" stop-color="#5d5470"/>
          <stop offset="0.5" stop-color="#8c8aa3"/>
          <stop offset="1" stop-color="#3b3740"/>
        </linearGradient>
        <linearGradient id="lab-tone" x1="0" y1="0" x2="1" y2="1">
          <stop offset="0" stop-color="#d7d9dc"/>
          <stop offset="0.6" stop-color="#eef0f2"/>
          <stop offset="1" stop-color="#9aa3ab"/>
        </linearGradient>
        <clipPath id="left-photo-clip"><circle cx="263" cy="358" r="118"/></clipPath>
        <clipPath id="right-photo-clip"><circle cx="428" cy="358" r="118"/></clipPath>
      </defs>

      <rect class="panel" x="16" y="16" width="564" height="887" fill="var(--panel)"/>
      <polygon class="slate-field" points="16,16 580,16 580,258 125,215 16,560" fill="var(--slate)"/>
      <polygon class="navy-wedge" points="60,16 406,16 372,186" fill="var(--navy)"/>
      <polygon class="slate-wedge" points="16,40 125,215 16,560" fill="var(--slate-dark)"/>
      <line x1="16" y1="40" x2="125" y2="215" stroke="var(--panel)" stroke-width="2"/>
      <line x1="125" y1="215" x2="372" y2="186" stroke="var(--panel)" stroke-width="2"/>
      <polygon class="stethoscope-photo" role="img" aria-label="Photo of a stethoscope on a pale blue surface"
               points="406,16 580,16 580,258 348,153" fill="var(--steel-photo)"/>

      <circle class="faint-mark" cx="40" cy="413" r="8" fill="none" stroke="var(--teal)" stroke-width="2"/>

      <circle cx="263" cy="358" r="134" fill="var(--panel)" stroke="var(--ink)" stroke-width="4" stroke-dasharray="12 8"/>
      <circle cx="428" cy="358" r="134" fill="var(--panel)" stroke="var(--ink)" stroke-width="4" stroke-dasharray="12 8"/>
      <g clip-path="url(#left-photo-clip)">
        <rect role="img" aria-label="Photo of doctors reviewing spinal X-ray images on a light board"
              x="145" y="240" width="236" height="236" fill="url(#xray-tone)"/>
      </g>
      <circle cx="428" cy="358" r="121" fill="var(--panel)"/>
      <g clip-path="url(#right-photo-clip)">
        <rect role="img" aria-label="Photo of a lab researcher in a white coat looking into a microscope"
              x="310" y="240" width="236" height="236" fill="url(#lab-tone)"/>
      </g>
    </svg>

    <div class="brand-badge"><span class="brand-name">KORVAX</span></div>

    <h1 class="headline headline-top">Medical Healthcare</h1>
    <h1 class="headline headline-bottom">Services &amp; Security</h1>

    <p class="tagline">A Universal Cyber Security Toolkit for the Health-Care Industry</p>

    <h2 class="audience-title">Why KORVAX is important for you?</h2>
    <span class="audience-item" style="left:43px; top:762px;">Industry (Security and IoT)</span>
    <span class="audience-item" style="left:43px; top:788px;">Medical organisations</span>
    <span class="audience-item" style="left:43px; top:813px;">Society</span>
    <span class="audience-item" style="left:308px; top:764px;">Research</span>
    <span class="audience-item" style="left:425px; top:764px;">Policy</span>
    <span class="audience-item" style="left:308px; top:788px;">International networks</span>
    <span class="audience-item" style="left:308px; top:813px;">Related EU-funded projects</span>

    <footer class="contact-band">
      <span class="contact-line" style="left:27px; top:1px;">Chirper: @ProjectKorvax</span>
      <span class="contact-line" style="left:27px; top:14px;">Facepage Page: korvax-project.eu</span>
      <span class="contact-line" style="left:160px; top:1px;">Linkwork Page: korvax-project</span>
      <span class="contact-line" style="left:160px; top:14px;">Vidstream: The korvax project eu</span>
      <span class="contact-line" style="left:296px; top:1px;">Web: https://korvax-project.eu/</span>
    </footer>
  </div>
</body>
</html>
```